Web Design Project

We are an IT System Integrator. We provide Korvin 450 ERP System, CRM etc. We also provide hardware, networking servicing. Please look at www.zolvantix.com.sg. They provide the same service as us. We like to redesign our web site. I will attached the color that I prefer for reference.

Our website is www.tadurk.com.sg.  It has been created about 14 years ago.  We are trying to revamp it with a new look and information.   The new website must be informative, fast.    I have attached an attachment which show the color that I prefer(brownish golden).   

Our competitor (www.zolvantix.com) is carrying the same trade as us.  They have all the informations In their website that we will like to have.  Therefore I recommend you to take a look at my competitor website and have a better   
understanding on the kind of information I would like to have for my new website.

This project is guarantee to the person with the best design.  We can have it guarantee.

Target Market(s)

Corporate and companies

Industry/Entity Type

Hardware

```html
<!DOCTYPE html>
<html lang="en">
<head>
<meta charset="utf-8">
<title>Tadurk Information System</title>
<link href="https://fonts.googleapis.com/css2?family=Ubuntu:wght@300;400;500;700&display=swap" rel="stylesheet">
<style>
:root{
  --gold-light:#e2b564;
  --gold:#cf9437;
  --gold-dark:#b97a22;
  --orange:#c8770f;
  --brown:#6e5320;
  --text:#6b6b6b;
  --grey-band:#d9d9d9;
  --white:#ffffff;
}
*{margin:0;padding:0;box-sizing:border-box}
html,body{width:1200px;height:932px;overflow:hidden;background:var(--white);font-family:"Ubuntu",sans-serif;color:var(--text)}
.page{position:relative;width:1200px;height:932px}

/* header */
.site-header{position:absolute;left:0;top:0;width:1200px;height:75px;background:linear-gradient(#fff,#eeeeee);border-bottom:1px solid #d6d6d6}
.brand{position:absolute;left:196px;top:16px;display:flex;align-items:center;gap:8px}
.brand-mark{width:40px;height:40px;border-radius:50%;background:var(--gold)}
.brand-name{color:var(--orange);font-weight:700;font-size:13px;line-height:14px;letter-spacing:.3px}
.social{position:absolute;left:938px;top:14px;display:flex;gap:5px}
.social span{width:19px;height:19px;border-radius:50%;border:1px solid #d9b47a;background:#fff}
.social span:first-child{background:var(--gold-dark);border-color:var(--gold-dark)}
.main-nav{position:absolute;left:546px;top:39px;display:flex;align-items:center}
.main-nav a{font-size:12.5px;font-weight:500;color:#4a4a4a;text-decoration:none;padding:0 8px;border-left:1px dotted #aaa;line-height:14px}
.main-nav a.active{background:linear-gradient(#e0a84e,var(--gold-dark));color:#fff;border:0;border-radius:11px;padding:6px 13px;margin-right:6px;font-size:12px}
.main-nav a.active + a{border-left:1px dotted #aaa}

/* hero */
.hero{position:absolute;left:0;top:75px;width:1200px;height:328px}
.hero-photo{position:absolute;inset:0;background:radial-gradient(ellipse at 45% 55%,#b98c50 0%,#6d5232 35%,#2c2620 70%,#1c1b1b 100%)}
.hero-title{position:absolute;left:197px;top:66px;color:#fff;font-weight:700;font-size:29px;line-height:37px;letter-spacing:-.5px;text-shadow:0 2px 4px rgba(0,0,0,.5)}
.hero-lead{position:absolute;left:197px;top:180px;width:300px;color:#e18f1a;font-size:10.5px;line-height:13.6px;font-weight:500}
.btn-quote{position:absolute;left:195px;top:234px;width:101px;height:26px;border-radius:13px;background:linear-gradient(#e6b05c,var(--gold-dark));color:#fff;font-weight:700;font-size:11.5px;text-align:center;line-height:26px}
.slider-dots{position:absolute;left:197px;top:300px;display:flex;gap:4px}
.slider-dots span{width:11px;height:11px;border-radius:50%;background:#fff}
.slider-dots span:first-child{background:var(--gold)}
.quote-box{position:absolute;left:765px;top:45px;width:231px;height:240px;background:linear-gradient(135deg,#c79a52,#a8742a);padding:0 22px}
.quote-box h2{color:#fff;font-size:16.5px;font-weight:500;margin:17px 0 15px 9px}
.quote-box .field{height:35px;background:#fff;border-radius:5px;margin-bottom:7px;font-size:10px;color:#aaa;padding:0 21px;line-height:35px;box-shadow:inset 0 1px 3px rgba(0,0,0,.25)}
.quote-box .submit{height:34px;margin-top:12px;border-radius:5px;background:linear-gradient(#f1c77d,#d5902f);color:#fff;font-size:16px;font-weight:500;text-align:center;line-height:34px}

/* welcome */
.welcome{position:absolute;left:197px;top:437px;width:512px}
.welcome h1{font-size:25px;font-weight:700;color:var(--brown);letter-spacing:-.3px}
.welcome h1 b{color:var(--orange);font-size:30px}
.welcome .rule{width:252px;border-top:2px dotted #ccc;margin:4px 0 9px}
.welcome p{font-size:10.6px;line-height:13.4px;font-weight:300;color:#666}
.divider{position:absolute;left:738px;top:460px;width:6px;height:128px;background:linear-gradient(90deg,rgba(0,0,0,.08),transparent)}

.news{position:absolute;left:795px;top:436px;width:201px}
.news h2{font-size:20px;font-weight:500;color:var(--orange);padding-bottom:5px;border-bottom:1px dotted #ccc;margin-bottom:12px}
.news-item{display:flex;gap:5px;border-bottom:1px dotted #ccc;padding-bottom:6px;margin-bottom:7px;width:175px}
.news-date{width:44px;position:relative;flex:none;height:40px}
.news-date .cal{position:absolute;left:1px;top:0;width:26px;height:24px;border:2px solid var(--brown);border-top-width:5px;border-radius:2px;font-size:13px;font-weight:700;color:#333;text-align:center;line-height:18px}
.news-date .month{position:absolute;left:-2px;top:27px;font-size:7px;color:#333}
.news-date .year{position:absolute;left:31px;top:10px;font-size:8px;color:#333;transform:rotate(-90deg);border-top:1px dotted #999}
.news-text strong{display:block;font-size:9px;font-weight:500;color:var(--brown)}
.news-text span{font-size:7.5px;line-height:10px;color:#888}

/* feature cards */
.features{position:absolute;left:197px;top:617px;display:flex;gap:47px}
.card{width:164px;text-align:center;position:relative}
.card-body{height:140px;border-radius:6px;background:linear-gradient(var(--gold-light),var(--gold-dark));padding-top:15px;position:relative}
.card-body::after{content:"";position:absolute;left:72px;bottom:-14px;border-left:11px solid transparent;border-right:11px solid transparent;border-top:14px solid var(--gold-dark)}
.card h3{color:#fff;font-weight:700;font-size:22px;letter-spacing:-.6px;line-height:26px}
.card p{color:#fff;font-size:11.5px;font-weight:300;line-height:12.5px;margin-top:4px}
.card .icon{width:47px;height:43px;margin:12px auto 0;background:#fff;border-radius:5px;display:flex;align-items:center;justify-content:center;box-shadow:0 1px 3px rgba(0,0,0,.3)}
.card .icon .word{font-size:9px;font-weight:700;color:var(--orange)}
.card a{display:block;margin-top:26px;font-size:10px;font-weight:700;color:var(--brown);text-decoration:underline}

/* partners */
.partners{position:absolute;left:0;top:820px;width:1200px;height:60px;background:var(--grey-band);box-shadow:0 6px 8px -4px rgba(0,0,0,.2)}
.partners h2{position:absolute;left:197px;top:17px;font-size:20px;font-weight:400;color:var(--brown);letter-spacing:-1px}
.partners h2 b{color:var(--orange);font-weight:700}
.partner-badge{position:absolute;top:16px;height:28px;background:#c4c4c4;border-radius:4px}

/* footer */
.site-footer{position:absolute;left:0;top:896px;width:1200px}
.copyright{position:absolute;left:197px;top:6px;font-size:11.5px;font-weight:300;color:#555}
.footer-nav{position:absolute;left:726px;top:3px;font-size:11px;font-weight:300;color:#555}
</style>
</head>
<body>
<div class="page">

  <header class="site-header">
    <div class="brand">
      <span class="brand-mark"></span>
      <span class="brand-name">TADURK<br>INFORMATION SYSTEM.</span>
    </div>
    <div class="social"><span></span><span></span><span></span></div>
    <nav class="main-nav">
      <a class="active" href="#">SOLUTIONS</a>
      <a href="#" style="border-left:0">HARDWARE</a>
      <a href="#">SERVICES</a>
      <a href="#">CLIENTS</a>
      <a href="#">ABOUT US</a>
      <a href="#">CONTACT US</a>
    </nav>
  </header>

  <section class="hero">
    <div class="hero-photo" role="img" aria-label="Businessman in a suit pointing at a glowing transparent touch screen"></div>
    <h1 class="hero-title">ACCOUNTING SOFTWARE,<br>NETWORKING, &amp; CONSULTING<br>ASSISTANCE.</h1>
    <p class="hero-lead">Tadurk Information Systems Pte Ltd (TIS) is professionally managed by a core group of visionaries and technologists with decades.</p>
    <div class="btn-quote">GET QUOTE!</div>
    <div class="slider-dots"><span></span><span></span><span></span><span></span><span></span></div>
    <form class="quote-box">
      <h2>Get a quote now!</h2>
      <div class="field">Name</div>
      <div class="field">Email</div>
      <div class="field">Mobile Number</div>
      <div class="submit">SUBMIT NOW</div>
    </form>
  </section>

  <section class="welcome">
    <h1>WELCOME TO <b>TIS.</b></h1>
    <div class="rule"></div>
    <p>Tadurk Information Systems Pte Ltd (TIS) is professionally managed by a core group of visionaries and technologists with decades of industry experience between them and backed by a team of trained professionals at all levels of operations. Perfection is a way of life at TIS. The organization has grown from a small beginning in 1993, to become a company of international repute for reliability. TIS has transformed from an LEDGRA Reseller to a company providing total IT solutions to companies in Singapore and the Asia region. TIS provides hardware maintenance, networking, software and consulting services.</p>
  </section>
  <div class="divider"></div>

  <aside class="news">
    <h2>Recent News</h2>
    <div class="news-item">
      <div class="news-date"><div class="cal">2</div><span class="month">MARCH</span><span class="year">2013</span></div>
      <div class="news-text"><strong>Lorem ipsum</strong><span>Lorem ipsum dolor sit amet, consectetuer adipiscing elit , sed diam nonummy nibh</span></div>
    </div>
    <div class="news-item">
      <div class="news-date"><div class="cal">4</div><span class="month">MARCH</span><span class="year">2013</span></div>
      <div class="news-text"><strong>Lorem ipsum</strong><span>Lorem ipsum dolor sit amet, consectetuer adipiscing elit , sed diam nonummy nibh</span></div>
    </div>
  </aside>

  <section class="features">
    <div class="card">
      <div class="card-body">
        <h3>COMPANY</h3><p>Lorem ipsum dolor sit<br>amet, consectetuer.</p>
        <div class="icon"><svg width="28" height="26" viewBox="0 0 28 26" fill="#c8770f"><path d="M14 1 27 8H1z"/><rect x="2" y="9" width="24" height="2"/><rect x="4" y="12" width="3" height="9"/><rect x="9.5" y="12" width="3" height="9"/><rect x="15.5" y="12" width="3" height="9"/><rect x="21" y="12" width="3" height="9"/><rect x="1" y="22" width="26" height="3"/></svg></div>
      </div>
      <a href="#">READ MORE</a>
    </div>
    <div class="card">
      <div class="card-body">
        <h3>PRODUCTS</h3><p>Lorem ipsum dolor sit<br>amet, consectetuer.</p>
        <div class="icon"><svg width="34" height="24" viewBox="0 0 34 24"><circle cx="25" cy="12" r="10" fill="none" stroke="#c8770f" stroke-width="2"/><circle cx="20" cy="12" r="10" fill="#fff" stroke="#c8770f" stroke-width="2"/><circle cx="12" cy="12" r="11" fill="#c8770f"/><text x="12" y="16.5" font-family="Ubuntu,sans-serif" font-weight="700" font-size="12" fill="#fff" text-anchor="middle">1</text></svg></div>
      </div>
      <a href="#">READ MORE</a>
    </div>
    <div class="card">
      <div class="card-body">
        <h3>LEDGRA</h3><p>Lorem ipsum dolor sit<br>amet, consectetuer.</p>
        <div class="icon"><span class="word">LEDGRA</span></div>
      </div>
      <a href="#">READ MORE</a>
    </div>
    <div class="card">
      <div class="card-body">
        <h3>SERVICES</h3><p>Lorem ipsum dolor sit<br>amet, consectetuer.</p>
        <div class="icon"><svg width="30" height="28" viewBox="0 0 30 28"><circle cx="10" cy="19" r="6" fill="none" stroke="#c8770f" stroke-width="4" stroke-dasharray="3 2"/><circle cx="10" cy="19" r="4" fill="#c8770f"/><circle cx="10" cy="19" r="1.8" fill="#fff"/><circle cx="21" cy="8" r="5" fill="none" stroke="#c8770f" stroke-width="3.5" stroke-dasharray="2.5 1.8"/><circle cx="21" cy="8" r="3.2" fill="#c8770f"/><circle cx="21" cy="8" r="1.4" fill="#fff"/></svg></div>
      </div>
      <a href="#">READ MORE</a>
    </div>
  </section>

  <section class="partners">
    <h2><b>TIS</b> PARTNERS :</h2>
    <div class="partner-badge" style="left:383px;width:38px;border-radius:50%;height:38px;top:11px"></div>
    <div class="partner-badge" style="left:496px;width:78px;height:24px;top:18px"></div>
    <div class="partner-badge" style="left:647px;width:38px;height:34px;top:13px"></div>
    <div class="partner-badge" style="left:762px;width:70px;height:26px;top:18px"></div>
    <div class="partner-badge" style="left:907px;width:89px;height:24px;top:19px"></div>
  </section>

  <footer class="site-footer">
    <p class="copyright">© 2011 Zolvantix Systems Pte Ltd. All rights reserved.</p>
    <p class="footer-nav">Home | Terms &amp; Conditions | Privacy Policy | Sitemap</p>
  </footer>

</div>
</body>
</html>
```